Existing Website Requiring new Pages

I have an existing word press website that was built using elementor.
Website: www.tallowcrestcare.com.au
I require the Vacancies page (https://www.tallowcrestcare.com.au/vacancies/) to be modified to display our new properties along with minor tweaks to how the information is presented.
The vacancies to be displayed are the exactly the same as those that are located on the homepage of QMR website (https://qmr.org.au/)
The new pages that link off the Vacancies tab will require custom design.
There are roughly 8 pages/properties to be incorporated. i wish for the design to be very similar to that displayed in the following link; https://www.polunda.com.au/vacancies/merrylands
Along with this the back end has not been updated for the last 3 years so it also requires some maintenance.
Website is in the disability industry and the custom pages will display information relative to Property Vacancies.
I have attached a ZIP file with some design guides, the information for each of the properties (which will need to be modified to show our business name Tallowcrest Care) and the example of how it is to look based off the Polunda website.
If you guys have any suggestions or ideas on how to make this more presentable or possible i'm open to your ideas.
Target Market(s)
People looking for SDA properties custom built for people with a disability
Industry/Entity Type
Disability
Coding
Coded - Design and coding required
Number of Pages Required
5+ page

```html
<!DOCTYPE html>
<html lang="en">
<head>
<meta charset="utf-8">
<title>Specialist Disability Accommodation SDA in Greystanes – Tallowcrest Care</title>
<link rel="stylesheet" href="https://fonts.googleapis.com/css2?family=Poppins:wght@400;500;600&family=Roboto:wght@400;500&display=swap">
<style>
:root{
  --ink:#1f1f24;
  --text:#3a3a40;
  --muted:#8a8d93;
  --orange:#fbb727;
  --coral:#f4856a;
  --pink:#f6406a;
  --purple:#6b4fd0;
  --lavender:#e4defa;
  --teal:#3fc4c8;
  --panel:#eef1f4;
  --line:#e1e4e8;
  --dark:#1e1e22;
}
*{box-sizing:border-box;margin:0;padding:0}
html,body{width:1200px;height:3929px;overflow:hidden;background:#fff}
body{position:relative;font-family:"Roboto",Arial,sans-serif;color:var(--text)}
.abs{position:absolute}
h1,h2,h3{font-family:"Poppins",Arial,sans-serif;color:var(--ink);font-weight:500}

/* header */
.brand{left:108px;top:30px;width:140px;display:flex;flex-direction:column;align-items:center;gap:10px}
.brand-mark{width:56px;height:56px;border-radius:50%;background:var(--pink)}
.brand-name{font-family:"Poppins",Arial,sans-serif;font-size:19px;font-weight:500;color:var(--purple);white-space:nowrap}
.nav{left:558px;top:74px;display:flex;gap:22px;font-family:"Poppins",Arial,sans-serif;font-size:11px;font-weight:600;letter-spacing:.8px;color:#4b4b55}
.nav .active{color:var(--coral)}
.deco{border-radius:40%;opacity:.35}

/* hero */
.tags{left:110px;top:195px;display:flex;gap:8px}
.tag{font-size:8px;font-weight:500;color:#fff;padding:2px 6px;text-transform:uppercase;letter-spacing:.2px}
.tag.purple{background:var(--purple)}
.tag.pink{background:var(--pink)}
.hero-title{left:110px;top:238px;width:460px;font-size:35px;line-height:43px;white-space:nowrap}
.hero-copy{left:110px;top:402px;width:340px;font-size:12px;line-height:23px;color:#333}
.hero-btns{left:110px;top:496px;display:flex;gap:9px}
.btn{display:inline-flex;align-items:center;justify-content:center;font-family:"Poppins",Arial,sans-serif;font-weight:600;color:#fff;border-radius:3px;font-size:11px;height:28px;padding:0 12px}
.btn.orange{background:var(--orange)}
.btn.purple{background:var(--purple)}
.btn.pink{background:var(--pink)}
.photo{background:linear-gradient(180deg,#7fb2e6 0%,#c6dcee 40%,#a89f8d 70%,#8d9a78 100%)}

/* content */
.section-title{font-size:29px;line-height:36px}
.copy{font-size:12px;line-height:23px;color:#333}
.feature{display:flex;align-items:center;gap:11px;font-size:12px;line-height:16px;color:#222}
.feature .ico{background:var(--lavender);border-radius:2px;flex:none}
.ico.lg{width:66px;height:66px}
.ico.sm{width:46px;height:40px}

/* enquiry form */
.enquire{left:674px;top:627px;width:387px;height:648px;background:var(--panel);border-radius:14px 14px 0 0;overflow:hidden}
.enquire-head{height:94px;background:var(--pink);text-align:center;color:#fff;padding-top:19px}
.enquire-head h3{color:#fff;font-size:29px;line-height:34px;font-weight:500}
.enquire-head p{font-family:"Poppins",Arial,sans-serif;font-size:12px;font-weight:600;letter-spacing:.8px;margin-top:4px}
.contact-row{display:flex;justify-content:center;gap:24px;margin-top:22px;font-size:15px;color:#222}
.contact-row span{display:flex;align-items:center;gap:9px}
.chip{width:25px;height:25px;border-radius:4px;background:var(--purple);display:flex;align-items:center;justify-content:center}
.field{position:absolute;left:31px;width:321px;height:37px;background:#fff;border:1px solid var(--line);border-radius:4px;font-size:10px;color:#555;padding:11px 13px}
.field.select{text-align:center;color:#666}
.field.select::after{content:"⌃";position:absolute;right:10px;top:8px;font-size:10px}
.field.msg{height:113px}
.submit{position:absolute;left:84px;top:572px;width:195px;height:44px;background:var(--orange);color:#fff;border-radius:4px;font-family:"Poppins",Arial,sans-serif;font-weight:600;font-size:14px;display:flex;align-items:center;justify-content:center;gap:10px}

/* gallery */
.gallery-main{left:110px;top:1473px;width:767px;height:566px;background:linear-gradient(135deg,#eceae6 0%,#f3f1ec 45%,#c9a27a 80%,#b48a62 100%)}
.gal-bar{left:891px;width:167px;height:12px;background:var(--orange);display:flex;justify-content:center;align-items:center}
.thumb{left:891px;width:167px;height:165px}

/* map */
.map{left:114px;top:2150px;width:949px;height:362px;background:linear-gradient(135deg,#eef0ec 0%,#e7ebe4 50%,#dfe6dd 100%)}

/* cards */
.card-img{height:308px}
.card-img.brick{background:linear-gradient(180deg,#8fb3dc 0%,#c9d5de 30%,#9a8a7c 65%,#7c7c72 100%)}
.card-img.grey{background:linear-gradient(180deg,#6f9cd6 0%,#c3d3e4 30%,#5d6066 60%,#9c9c98 100%)}
.card-tags{position:absolute;top:10px;display:flex;gap:5px}
.card-title{font-family:"Poppins",Arial,sans-serif;font-size:11px;font-weight:600;color:#222}
.card-sub{font-size:10px;color:#666;margin-top:2px}
.card-feat{font-size:9px;color:#333;margin-top:7px;line-height:15px;text-transform:uppercase}
.details{position:absolute;width:72px;height:29px;background:var(--orange);color:#fff;border-radius:3px;font-family:"Poppins",Arial,sans-serif;font-weight:600;font-size:11px;display:flex;align-items:center;justify-content:center}

/* footer */
.footer{left:0;top:3599px;width:1200px;height:267px;background:#fff;border-top:1px solid #f1f1f1}
.foot-contact{font-size:11px;color:#777;line-height:21px}
.foot-contact span{color:var(--pink);margin-right:6px}
.social{width:26px;height:26px;border-radius:50%;background:#1e2f8a}
.foot-col h4{font-family:"Poppins",Arial,sans-serif;font-size:12px;font-weight:500;color:#222;letter-spacing:.6px;border-left:3px solid var(--purple);padding-left:10px;line-height:13px}
.foot-col ul{list-style:none;margin-top:20px}
.foot-col li{font-size:11px;color:#888;line-height:15px;padding:7px 0 8px;border-bottom:1px solid #eee}
.copyright{left:0;top:3866px;width:1200px;height:63px;background:var(--dark);color:#aaa;font-size:9px;text-align:center;line-height:63px}
.totop{left:1142px;top:3501px;width:29px;height:28px;background:#999;display:flex;align-items:center;justify-content:center}
</style>
</head>
<body>

<!-- header -->
<div class="abs brand">
  <div class="brand-mark"></div>
  <div class="brand-name">Tallowcrest Care</div>
</div>
<nav class="abs nav">
  <span class="active">HOME</span><span>ABOUT US</span><span>WHAT WE DO ⌄</span><span>REFERRALS</span><span>FEEDBACK</span><span>CONTACT US</span>
</nav>

<div class="abs deco" style="left:28px;top:192px;width:64px;height:54px;background:radial-gradient(circle,#f25ca0,#fff 70%)" role="img" aria-label="Decorative pink butterflies"></div>

<!-- hero -->
<div class="abs tags">
  <span class="tag purple">Featured</span><span class="tag pink">Almost full - apply now!</span><span class="tag pink">Apply now</span>
</div>
<h1 class="abs hero-title">Specialist Disability<br>Accommodation<br>SDA in Greystanes</h1>
<p class="abs hero-copy">Fully Accessible and High Physical Support apartments in Greystanes for NDIS participants looking for Specialist Disability Accommodation (SDA).</p>
<div class="abs hero-btns">
  <span class="btn orange">Enquire Now</span>
  <span class="btn purple">Download Property Brochure</span>
</div>
<div class="abs photo" style="left:491px;top:154px;width:569px;height:418px" role="img" aria-label="Exterior render of the two-storey SDA home in Greystanes with driveway and garden"></div>

<!-- property details -->
<h2 class="abs section-title" style="left:110px;top:638px">Property Details</h2>
<p class="abs copy" style="left:110px;top:704px;width:500px">Set on 760sqm of land in the Greater Western Sydney suburb of Greystanes, this Specialist Disability Accommodation (SDA) is designed as a Fully Accessible (FA) / High Physical Support (HPS) home. The east facing home accommodation availability includes:</p>

<h2 class="abs section-title" style="left:108px;top:830px">Property Features</h2>
<div class="abs feature" style="left:110px;top:900px"><div class="ico lg" role="img" aria-label="Garden icon"></div>Sanctuary<br>garden</div>
<div class="abs feature" style="left:284px;top:900px"><div class="ico lg" role="img" aria-label="Lift icon"></div>Internal lift</div>
<div class="abs feature" style="left:427px;top:900px"><div class="ico lg" role="img" aria-label="Seedling icon"></div>Vegetable<br>and herb garden</div>
<div class="abs feature" style="left:110px;top:1017px"><div class="ico lg" role="img" aria-label="Park bench and tree icon"></div>Open space<br>for relaxation and play</div>
<div class="abs feature" style="left:317px;top:1017px"><div class="ico lg" role="img" aria-label="Group of people icon"></div>Communal area for gatherings<br>and shared activities</div>

<h2 class="abs section-title" style="left:110px;top:1163px">Apartment Features</h2>
<div class="abs feature" style="left:110px;top:1241px"><div class="ico sm" role="img" aria-label="Air conditioner icon"></div>5star-rated<br>air conditioning</div>
<div class="abs feature" style="left:267px;top:1241px"><div class="ico sm" role="img" aria-label="Kitchen icon"></div>Fitted-out kitchen</div>
<div class="abs feature" style="left:435px;top:1241px"><div class="ico sm" role="img" aria-label="Bathroom icon"></div>Bathroom with<br>accessible facilities</div>

<!-- enquiry form -->
<div class="abs enquire">
  <div class="enquire-head">
    <h3>Enquire Now</h3>
    <p>ENQUIRE ABOUT THIS PROPERTY</p>
  </div>
  <div class="contact-row">
    <span><i class="chip"><svg width="13" height="13" viewBox="0 0 24 24"><path fill="#fff" d="M6.6 10.8a15 15 0 0 0 6.6 6.6l2.2-2.2c.3-.3.7-.4 1-.2 1.1.4 2.3.6 3.6.6.6 0 1 .4 1 1V20c0 .6-.4 1-1 1A17 17 0 0 1 3 4c0-.6.4-1 1-1h3.5c.6 0 1 .4 1 1 0 1.3.2 2.5.6 3.6.1.3 0 .7-.2 1z"/></svg></i>1300 482 716</span>
    <span><i class="chip"><svg width="13" height="11" viewBox="0 0 24 18"><path fill="#fff" d="M0 0h24v18H0z"/><path fill="none" stroke="#6b4fd0" stroke-width="2" d="M1 1l11 8 11-8"/></svg></i>info@qmr.org.au</span>
  </div>
  <div class="field" style="top:167px">First Name *</div>
  <div class="field" style="top:223px">Last Name *</div>
  <div class="field" style="top:276px">Phone*</div>
  <div class="field" style="top:331px">Email *</div>
  <div class="field select" style="top:384px">————— Select Services —————</div>
  <div class="field msg" style="top:437px">Message</div>
  <div class="submit">ENQUIRE NOW <span>⟶</span></div>
</div>

<div class="abs deco" style="left:1000px;top:1310px;width:170px;height:140px;background:radial-gradient(circle,#b15dd0,#fff 70%)" role="img" aria-label="Decorative flock of birds"></div>

<!-- gallery -->
<h2 class="abs section-title" style="left:110px;top:1402px">Property Gallery</h2>
<div class="abs gallery-main" role="img" aria-label="Open-plan living and kitchen area with resident in wheelchair at the patio door"></div>
<div class="abs gal-bar" style="top:1471px"><svg width="10" height="6" viewBox="0 0 10 6"><path d="M1 5l4-4 4 4" stroke="#222" stroke-width="1.5" fill="none"/></svg></div>
<div class="abs thumb" style="top:1491px;background:linear-gradient(135deg,#d9dcd6,#7b8a6d)" role="img" aria-label="Resident in wheelchair on the balcony"></div>
<div class="abs thumb" style="top:1673px;background:linear-gradient(135deg,#eef0ee,#a9c49a)" role="img" aria-label="Accessible bathroom with green tiles"></div>
<div class="abs thumb" style="top:1853px;background:linear-gradient(135deg,#e9e7e2,#8a9a9f)" role="img" aria-label="Resident in wheelchair in the kitchen"></div>
<div class="abs gal-bar" style="top:2025px"><svg width="10" height="6" viewBox="0 0 10 6"><path d="M1 1l4 4 4-4" stroke="#222" stroke-width="1.5" fill="none"/></svg></div>

<!-- map -->
<h2 class="abs section-title" style="left:116px;top:2079px">SDA in Greystanes</h2>
<div class="abs map" role="img" aria-label="Street map of Greystanes showing the property location"></div>

<!-- browse -->
<div class="abs deco" style="left:0;top:2540px;width:110px;height:140px;background:radial-gradient(circle,#8a63d8,#fff 70%)" role="img" aria-label="Decorative flock of birds"></div>
<h2 class="abs section-title" style="left:116px;top:2548px">Browse More Properties</h2>

<div class="abs" style="left:110px;top:2620px;width:466px">
  <div class="card-img photo" role="img" aria-label="Greystanes SDA home exterior"></div>
  <div class="card-tags" style="left:10px"><span class="tag purple">Featured</span></div>
  <div class="card-tags" style="right:10px"><span class="tag pink">Almost full - apply now!</span><span class="tag pink">Apply now</span></div>
  <div style="margin-top:37px"><div class="card-title">SDA in Greystanes</div><div class="card-sub">Greystanes</div><div class="card-feat">Fully accessible, high physical support</div></div>
  <div class="details" style="left:395px;top:346px">Details</div>
</div>

<div class="abs" style="left:627px;top:2620px;width:434px">
  <div class="card-img brick" role="img" aria-label="Werrington townhouse front with balcony"></div>
  <div class="card-tags" style="left:10px"><span class="tag purple">Featured</span></div>
  <div class="card-tags" style="right:10px"><span class="tag pink">Available now</span><span class="tag pink">Current vacancy</span></div>
  <div style="margin-top:37px"><div class="card-title">SDA in Werrington</div><div class="card-sub">Werrington</div><div class="card-feat">Fully accessible, improved liveability</div></div>
  <div class="details" style="left:358px;top:346px">Details</div>
</div>

<div class="abs" style="left:110px;top:3056px;width:466px">
  <div class="card-img grey" role="img" aria-label="Wentworthville brick villas exterior"></div>
  <div class="card-tags" style="left:10px"><span class="tag purple">Featured</span></div>
  <div class="card-tags" style="right:10px"><span class="tag pink">Available now</span><span class="tag pink">New construction</span></div>
  <div style="margin-top:35px"><div class="card-title">SDA villas in Wentworthville</div><div class="card-sub">Wentworthville</div><div class="card-feat">Fully accessible, high physical support,<br>improved liveability</div></div>
  <div class="details" style="left:395px;top:344px">Details</div>
</div>

<div class="abs" style="left:627px;top:3056px;width:434px">
  <div class="card-img brick" role="img" aria-label="West Pennant Hills home exterior with garage"></div>
  <div class="card-tags" style="right:10px"><span class="tag pink">Current vacancy</span><span class="tag pink">Apply now</span></div>
  <div style="margin-top:35px"><div class="card-title">SDA in West Pennant Hills</div><div class="card-sub">West Pennant Hills</div><div class="card-feat">High physical support</div></div>
  <div class="details" style="left:358px;top:344px">Details</div>
</div>

<div class="abs" style="left:480px;top:3492px;display:flex;gap:8px">
  <span class="btn purple" style="width:142px">View All Vacancies</span>
  <span class="btn pink" style="width:90px">Contact Us</span>
</div>

<div class="abs deco" style="left:1000px;top:3440px;width:170px;height:140px;background:radial-gradient(circle,#b15dd0,#fff 70%)" role="img" aria-label="Decorative flock of birds"></div>
<div class="abs totop"><svg width="10" height="6" viewBox="0 0 10 6"><path d="M1 5l4-4 4 4" stroke="#fff" stroke-width="1.5" fill="none"/></svg></div>

<!-- footer -->
<footer class="abs footer">
  <div class="abs brand" style="left:140px;top:52px">
    <div class="brand-mark"></div>
    <div class="brand-name">Tallowcrest Care</div>
  </div>
  <div class="abs foot-contact" style="left:140px;top:182px">
    <div><span>✉</span>Email: info@tallowcrestcare.com.au</div>
    <div><span>✆</span>Phone: +61 0400 318 562</div>
    <div><span>◷</span>Operating Hours: 9AM To 5PM Monday - Friday</div>
  </div>
  <div class="abs social" style="left:521px;top:51px;background:#5b2d8c"></div>
  <div class="abs social" style="left:521px;top:89px"></div>
  <div class="abs social" style="left:521px;top:127px;background:#222"></div>
  <div class="abs social" style="left:521px;top:165px"></div>
  <div class="abs foot-col" style="left:605px;top:44px;width:208px">
    <h4>ACCOMMODATION</h4>
    <ul>
      <li>Supported Independent Living (SIL)</li>
      <li>Specialist Disability Accommodation (SDA)</li>
      <li>Short term Accommodation<br>(Respite)</li>
      <li>Vacancies</li>
    </ul>
  </div>
  <div class="abs foot-col" style="left:837px;top:44px;width:210px">
    <h4>WHAT WE DO</h4>
    <ul>
      <li>In Home Care</li>
      <li>Social &amp; Community Services</li>
      <li>Therapeutic Supports</li>
      <li>Support Coordination</li>
      <li>Home Modifications</li>
    </ul>
  </div>
</footer>
<div class="abs copyright">© Copyright 2021 | Tallowcrest Care | All Rights Reserved.</div>

</body>
</html>
```